National Mission Critical Construction Contractor needs Stationery Design to make a bold statement

We are a small commercial construction company, working primarily in mission critical facilities across the U.S.. We have exciting corporate changes going an and a new logo and office space so we need new stationery. The final design should incorporate our new logo and invoke a fresh, high-tech feel while looking simple and modern.

Industry/Entity Type

Construction

Contact Information for Business Card

We are required to list our state licensing qualifications on the back of our card.

Font styles to use
Sans Serif

Requirements
Must have
• We need to have a design for second page of stationery, envelopes both standard and with a window and for a 3 x 4 notepad.

```html
<!DOCTYPE html>
<html lang="en">
<head>
<meta charset="utf-8">
<title>Clear Ridge Business Card</title>
<link rel="stylesheet" href="https://fonts.googleapis.com/css2?family=Montserrat:wght@500&family=Open+Sans:wght@400;600&display=swap">
<style>
  :root {
    --backdrop: #333333;
    --backdrop-light: #5a5a5a;
    --paper: #f6f6f6;
    --brand-blue: #1469b8;
    --brand-blue-deep: #1264b0;
    --accent-blue: #2a9de0;
    --ink: #4f4f4f;
    --rule: #d4d4d4;
    --white: #ffffff;
  }
  * { margin: 0; padding: 0; box-sizing: border-box; }
  html, body {
    width: 1200px; height: 750px; overflow: hidden;
    background: radial-gradient(ellipse 60% 55% at 50% 48%, var(--backdrop-light), var(--backdrop));
  }
  .stage { position: relative; width: 1200px; height: 750px; }
  .card {
    position: absolute; top: 228px;
    width: 461px; height: 262px; border-radius: 14px;
  }
  .card-front { left: 124px; background: var(--paper); }
  .card-back { left: 618px; background: var(--brand-blue-deep); }

  .brand { position: absolute; text-align: center; }
  .brand-mark { display: block; margin: 0 auto; border-radius: 50%; }
  .brand-name {
    font-family: "Montserrat", sans-serif; font-weight: 500;
    letter-spacing: 0.5px; line-height: 1; white-space: nowrap;
  }
  .brand-tagline {
    font-family: "Montserrat", sans-serif; font-weight: 500;
    line-height: 1; white-space: nowrap;
    padding-top: 5px; margin-top: 4px;
  }

  .card-front .brand { left: 44px; top: 81px; width: 188px; }
  .card-front .brand-mark { width: 59px; height: 59px; border: 2.5px solid var(--brand-blue); }
  .card-front .brand-name { color: var(--brand-blue); font-size: 24px; margin-top: 9px; }
  .card-front .brand-tagline {
    color: var(--brand-blue); font-size: 7.5px; letter-spacing: 2.1px;
    border-top: 1px solid var(--rule); display: inline-block;
  }

  .divider {
    position: absolute; left: 242px; top: 48px;
    width: 1px; height: 168px; background: var(--rule);
  }

  .contact { position: absolute; left: 262px; top: 46px; font-family: "Open Sans", sans-serif; color: var(--ink); }
  .contact-name { color: var(--brand-blue); font-weight: 600; font-size: 17.5px; line-height: 1.2; }
  .contact-role { color: var(--accent-blue); font-size: 13px; line-height: 1.3; margin-bottom: 8px; }
  .contact-address { font-size: 12.5px; line-height: 1.35; margin-bottom: 4px; }
  .contact-list { list-style: none; font-size: 12.5px; }
  .contact-list li { display: flex; align-items: center; height: 17.6px; }
  .contact-list svg { width: 11px; height: 11px; margin-right: 7px; fill: var(--brand-blue); flex: none; }

  .card-back .brand { left: 70px; top: 70px; width: 320px; }
  .card-back .brand-mark { width: 67px; height: 67px; border: 2.5px solid var(--white); }
  .card-back .brand-name { color: var(--white); font-size: 27px; margin-top: 13px; }
  .card-back .brand-tagline {
    color: var(--white); font-size: 8.5px; letter-spacing: 2.4px;
    border-top: 1.5px solid var(--white); display: inline-block;
  }

  .back-web {
    position: absolute; left: 0; width: 100%; top: 218px; text-align: center;
    font-family: "Open Sans", sans-serif; color: var(--white);
    font-size: 11.5px; letter-spacing: 3.6px;
  }
</style>
</head>
<body>
<main class="stage">

  <section class="card card-front">
    <div class="brand">
      <span class="brand-mark"></span>
      <div class="brand-name">CLEAR RIDGE</div>
      <div class="brand-tagline">CONSTRUCTION MANAGEMENT</div>
    </div>

    <div class="divider"></div>

    <div class="contact">
      <div class="contact-name">Dana Whitfield</div>
      <div class="contact-role">CEO/Founder</div>
      <div class="contact-address">2140 Harbor View Road<br>Juneau, Alaska 99801</div>
      <ul class="contact-list">
        <li><svg viewBox="0 0 12 12"><path d="M2.4 0.6l2 2.2-1 1.4c.7 1.6 1.8 2.7 3.4 3.4l1.4-1 2.2 2-1.2 2.2C5 10.6 1.4 7 .4 1.8z"/></svg>907 555 0142</li>
        <li><svg viewBox="0 0 12 12"><path d="M3 0h6a1 1 0 0 1 1 1v10a1 1 0 0 1-1 1H3a1 1 0 0 1-1-1V1a1 1 0 0 1 1-1zm.4 1.4v8h5.2v-8z"/></svg>907 555 0187</li>
        <li><svg viewBox="0 0 12 12"><path d="M3 0h6v3H3zM1 4h10v5H1zM2.5 10h7v2h-7z"/></svg>907 555 0163</li>
        <li><svg viewBox="0 0 12 12"><path d="M0 2h12v8H0zm1.2 1.2L6 6.6l4.8-3.4z" fill-rule="evenodd"/></svg>hello@clearridgebuild.com</li>
        <li><svg viewBox="0 0 12 12"><circle cx="6" cy="6" r="6"/><path d="M0.5 6h11M6 .5c-2 3-2 8 0 11M6 .5c2 3 2 8 0 11" stroke="#f6f6f6" stroke-width="0.9" fill="none"/></svg>www.clearridgebuild.com</li>
      </ul>
    </div>
  </section>

  <section class="card card-back">
    <div class="brand">
      <span class="brand-mark"></span>
      <div class="brand-name">CLEAR RIDGE</div>
      <div class="brand-tagline">CONSTRUCTION MANAGEMENT</div>
    </div>
    <div class="back-web">www.clearridgebuild.com</div>
  </section>

</main>
</body>
</html>
```